Personal Chef Needs a Good Web Design

Hi everyone!
My name is Leo, I work as a private chef for last 10 years, traveling all around the world and cooking in private megayacht and villas.
I'm about to settle down in my hometown in Europe for a while. And therefore I need a website that will show my story, pics and recipes, nutritional advices and of course offer a Personal and Private Chef services( working for 4-5 families and bringing delicious food to their house).
My clients are extremely rich folks, but usually are down to earth ones.
I believe, the web site should be focused on attention to:
-VIP person's wife( as she is usually responsible for food for family) and be simple.
-to famous people agents and be on high level.

There will be about 10 different menus and 6 different service offers

--UPDATE--
Logo Design:
+My thoughts are- printed structure of the vegetable or fruit on a white font. Like you slice the buffalo tomato, put it in red paint and print it on the edge of the page. See attached files named logo. Can be any nice structured thing, like tomato, lemon, red cabbage etc.
+Classic logos with chef's hat or knives are good too.
+Need to have the space for me to add the name( the fonts can be provided)

Target Market(s)

Private person. 80% Russian clients.

Industry/Entity Type

Cooking

Coding

Coded - Design and coding required

Number of Pages Required

3 page

Requirements
Must have
• Contact form/ Request back call/ Schedule a free consultation
Nice to have
• The client will need to choose straight ahead from the range of services I offer, like:
• -Private Chef( cooking only for the client)
• -Personal Chef( cooking for around 5 clients, bringing the ready to be heated food to their door)
• -Romantic dinner for two
• -Professional Sommelier service
• -Build your kitchen( offering design, equipment and that will fit your requirements)
• -Other( flowers, waiters, barista, equipment rental)
• So this column should go right after the introduction/aboutme part and will lead to separate pages with how-it-works thing for each.

```html
<!DOCTYPE html>
<html lang="en">
<head>
<meta charset="utf-8">
<title>Leo Chef — Private Chef</title>
<link href="https://fonts.googleapis.com/css2?family=Roboto+Slab:wght@300;400&family=Open+Sans:wght@400;600&display=swap" rel="stylesheet">
<style>
  :root{
    --red:#a90a1a;
    --red-btn:#c0141f;
    --white:#ffffff;
    --ink:#222222;
    --grey:#666666;
    --light-grey:#999999;
    --gold:#e9a21b;
    --dark:#1c1410;
  }
  *{margin:0;padding:0;box-sizing:border-box}
  html,body{width:1200px;height:3321px;overflow:hidden;background:var(--white)}
  body{position:relative;font-family:"Open Sans",Arial,sans-serif;color:var(--ink)}
  .slab{font-family:"Roboto Slab",Georgia,serif;font-weight:300}
  .abs{position:absolute}
  .center{left:0;width:1200px;text-align:center}

  /* header */
  .site-header{position:absolute;top:0;left:0;width:1200px;height:73px;background:var(--white)}
  .brand{position:absolute;left:100px;top:14px;display:flex;align-items:center;gap:16px}
  .brand-dot{width:46px;height:46px;border-radius:50%;background:var(--red-btn)}
  .brand-name{font-family:"Roboto Slab",Georgia,serif;font-weight:400;font-size:30px;color:var(--ink)}
  .nav-link{position:absolute;top:29px;font-size:12px;letter-spacing:.5px;color:var(--ink);transform:translateX(-50%);white-space:nowrap}
  .btn{background:var(--red-btn);color:var(--white);font-size:13px;font-weight:600;display:flex;align-items:center;justify-content:center;border-radius:3px;letter-spacing:.5px}
  .nav-book{position:absolute;left:994px;top:22px;width:106px;height:34px;font-size:12px}

  /* hero */
  .hero{position:absolute;top:73px;left:0;width:1200px;height:591px;
    background:radial-gradient(ellipse at 55% 60%,#6b3a1e 0%,#3a2014 35%,#140c08 75%)}
  .hero-arrow{position:absolute;top:322px;width:38px;height:38px;border-radius:50%;border:1px solid rgba(255,255,255,.35)}
  .hero-title{top:243px;font-size:72px;color:var(--white)}
  .hero-sub{top:325px;font-size:40px;color:var(--white)}
  .hero-btn{position:absolute;left:522px;top:405px;width:158px;height:44px}

  /* how it works */
  .how{position:absolute;top:664px;left:0;width:1200px;height:405px;background:var(--red)}
  .how-wave{position:absolute;top:1068px;left:0}
  .how-title{top:732px;font-size:48px;color:var(--white)}
  .how-text{position:absolute;left:190px;width:820px;text-align:center;font-size:12.5px;line-height:26.5px;color:var(--white)}

  /* menus */
  .section-title{font-size:38px;color:var(--ink)}
  .menus-title{top:1160px}
  .menus-sub{top:1218px;font-size:15px;color:var(--grey)}
  .menu-card{position:absolute;top:1291px;width:318px;height:343px}
  .menu-card .frame{position:absolute;inset:12px;border:3px solid rgba(255,255,255,.85)}
  .menu-card .label{position:absolute;left:0;right:0;top:145px;text-align:center;font-size:38px;color:var(--white)}

  /* specials */
  .specials{position:absolute;top:1716px;left:0;width:1200px;height:571px;
    background:radial-gradient(ellipse at 50% 40%,#4a2c16 0%,#2a1a10 55%,#120b07 100%)}
  .specials-title{top:1804px;font-size:38px;color:var(--white)}
  .offer-img{position:absolute;top:1897px;width:312px;height:206px;border:4px solid var(--red-btn)}
  .offer-name{position:absolute;top:2125px;width:312px;text-align:center;font-size:22px;color:var(--gold);font-weight:400}
  .offer-text{position:absolute;top:2162px;width:312px;text-align:center;font-size:13px;line-height:24px;color:var(--white)}

  /* testimonials */
  .clients-title{top:2376px}
  .clients-text{position:absolute;left:262px;width:676px;top:2446px;text-align:center;font-size:15.5px;line-height:27px;color:var(--grey)}
  .chev{position:absolute;top:2598px}
  .avatar{position:absolute;left:463px;top:2566px;width:92px;height:92px;border-radius:50%;background:linear-gradient(#c9a98f,#6b5a50);border:3px solid #e6e6e6}
  .client-name{position:absolute;left:578px;top:2586px;font-size:21px;color:var(--ink);font-family:"Roboto Slab",Georgia,serif;font-weight:400}
  .client-role{position:absolute;left:578px;top:2620px;font-size:12px;color:var(--light-grey);font-family:"Roboto Slab",Georgia,serif}

  /* call */
  .call{position:absolute;top:2739px;left:0;width:1200px;height:361px;
    background:linear-gradient(180deg,#2b2a26 0%,#1e1d1a 60%,#2a2723 100%)}
  .call-title{top:2838px;font-size:38px;color:var(--white)}
  .call-line{top:2896px;font-size:17px;color:var(--white);display:flex;justify-content:center;align-items:baseline;gap:16px}
  .call-phone{font-size:29px;color:var(--gold)}
  .call-btn{position:absolute;left:519px;top:2954px;width:164px;height:46px}

  /* footer */
  .social{position:absolute;top:3159px;width:33px;height:33px;border-radius:50%}
  .foot-link{position:absolute;top:3224px;font-size:12px;color:var(--ink);transform:translateX(-50%);font-family:"Roboto Slab",Georgia,serif}
  .copyright{top:3262px;font-size:11.5px;color:var(--ink);font-family:"Roboto Slab",Georgia,serif}
</style>
</head>
<body>

<header class="site-header">
  <div class="brand"><span class="brand-dot"></span><span class="brand-name">Leo Chef</span></div>
  <nav>
    <span class="nav-link" style="left:467px">HOME</span>
    <span class="nav-link" style="left:576px">ABOUT US</span>
    <span class="nav-link" style="left:695px">SERVICES</span>
    <span class="nav-link" style="left:802px">MENU</span>
    <span class="nav-link" style="left:919px">CONTACT US</span>
    <span class="btn nav-book">BOOK NOW!</span>
  </nav>
</header>

<section class="hero" role="img" aria-label="Close-up of a plated grilled lamb rack with herbs and roasted carrots"></section>
<span class="hero-arrow" style="left:56px"></span>
<span class="hero-arrow" style="left:1108px"></span>
<h1 class="abs center slab hero-title">Leo Chef</h1>
<p class="abs center slab hero-sub">I work as a private chef for last 10 years</p>
<span class="btn hero-btn">CONTACT HERE!</span>

<section class="how"></section>
<svg class="how-wave" width="1200" height="34" viewBox="0 0 1200 34">
  <path d="M0 0 H1200 V2 C900 2 720 10 600 32 C480 10 300 2 0 2 Z" fill="#a90a1a"/>
</svg>
<h2 class="abs center slab how-title">How it works</h2>
<p class="how-text" style="top:813px">Our first consultation will be in your home. We will discuss any food preferences you may have, as well as any allergy or dietary needs. At this time we will also discuss what kind of meals you like, from meat and potatoes to all organic, vegan and vegetarian meals or international cuisine like Italian or Mexican . If you have concerns about your diet we can work with any restrictions you have.</p>
<p class="how-text" style="top:919px">On your scheduled cook date We will prepare your meals in our commercial kitchen and drop them off to you at your convenience. Your meals will be chilled, packaged, labeled and stored in your refrigerator or freezer with easy instructions for heating. Meals can be packaged in single servings or family style. All meals will have special heating instructions which most only require you heating it up in the oven.</p>

<h2 class="abs center slab section-title menus-title">Our Menus</h2>
<p class="abs center menus-sub">I work as a private chef for last 10 years, traveling all around the world and cooking in private megayacht and villas.</p>
<div class="menu-card" style="left:100px;background:linear-gradient(135deg,#b9b2a6,#7fa04a 55%,#cfcfc8)" role="img" aria-label="Fresh salad with tomatoes and lettuce in a white bowl">
  <span class="frame"></span><span class="label slab">Breakfast</span></div>
<div class="menu-card" style="left:441px;background:linear-gradient(135deg,#3a2a14,#b0621e 50%,#5a3210)" role="img" aria-label="Roasted chicken with golden potatoes">
  <span class="frame"></span><span class="label slab">Lunch</span></div>
<div class="menu-card" style="left:784px;background:linear-gradient(135deg,#6b4a2a,#8a5a3a 50%,#c9b8a0)" role="img" aria-label="Tacos with shredded meat on a plate">
  <span class="frame"></span><span class="label slab">Dinner</span></div>

<section class="specials" role="img" aria-label="Blurred restaurant table with food in warm light"></section>
<h2 class="abs center slab specials-title">Our Specials Offers</h2>
<div class="offer-img" style="left:100px;background:linear-gradient(135deg,#3a2420,#6a1820 50%,#2a2a30)" role="img" aria-label="Two glasses of red wine raised in a toast"></div>
<div class="offer-img" style="left:444px;background:linear-gradient(135deg,#2a1a12,#7a5030 50%,#20140e)" role="img" aria-label="Friends enjoying a meal at a restaurant table"></div>
<div class="offer-img" style="left:789px;background:linear-gradient(135deg,#5a4a40,#3f7a2a 50%,#c4b8a8)" role="img" aria-label="Plate of green salad with tomatoes"></div>
<h3 class="offer-name slab" style="left:100px">Wine Special</h3>
<h3 class="offer-name slab" style="left:444px">Happy Hour Discounts</h3>
<h3 class="offer-name slab" style="left:789px">Stay Healthy</h3>
<p class="offer-text" style="left:100px">Lorem Ipsum is simply dummy text of the<br>printing and typesetting industry.</p>
<p class="offer-text" style="left:444px">Lorem Ipsum is simply dummy text of the<br>printing and typesetting industry.</p>
<p class="offer-text" style="left:789px">Lorem Ipsum is simply dummy text of the<br>printing and typesetting industry.</p>

<h2 class="abs center slab section-title clients-title">What our client’s say</h2>
<p class="clients-text">Lorem Ipsum is simply dummy text of the printing and typesetting industry. Lorem Ipsum has been the industry's standard dummy text ever since the 1500s, when an unknown printer took a galley of type and scrambled it to make a type specimen book...</p>
<svg class="chev" style="left:417px" width="16" height="26" viewBox="0 0 16 26"><path d="M13 2 L3 13 L13 24" fill="none" stroke="#555" stroke-width="2.5"/></svg>
<svg class="chev" style="left:766px" width="16" height="26" viewBox="0 0 16 26"><path d="M3 2 L13 13 L3 24" fill="none" stroke="#555" stroke-width="2.5"/></svg>
<div class="avatar" role="img" aria-label="Portrait photo of the client"></div>
<p class="client-name">Marcus Hale</p>
<p class="client-role">Business man</p>

<section class="call" role="img" aria-label="Dim outdoor restaurant terrace with tables"></section>
<h2 class="abs center slab call-title">Make a call for book</h2>
<p class="abs center slab call-line"><span>Lorem Ipsum is simply dummy text of the printing</span><span class="call-phone">( 988 ) 555 - 0142</span></p>
<span class="btn call-btn">CONTACT HERE!</span>

<footer>
  <span class="social" style="left:501px;background:#2c5aa8"></span>
  <span class="social" style="left:541px;background:#1f6f99"></span>
  <span class="social" style="left:581px;background:#e9a21b"></span>
  <span class="social" style="left:623px;background:#3aa3dd"></span>
  <span class="social" style="left:663px;background:#d42424"></span>
  <span class="foot-link" style="left:379px">Home</span>
  <span class="foot-link" style="left:483px">About us</span>
  <span class="foot-link" style="left:594px">Services</span>
  <span class="foot-link" style="left:695px">Menu</span>
  <span class="foot-link" style="left:806px">Contact Us</span>
  <p class="abs center copyright">Copyright © 2016, Leo Chef. All Rights Reserved.</p>
</footer>

</body>
</html>
```